Simple landing page for Brambles cookbook

I need a one page landingpage where customers can order the cookbook.
This is a cookbook of a collection of recipes from our deli that we used to run.
I need a landing page where customers can come and order the book. I also need it coded. I already have the domain through hostwell.
I can send the file of the book through wetransfer. It's too big to upload here. Just so you get the feel that I am looking for.
I attached a simple text as an introduction to the page. But I am open to any suggestions. I want it all to be about the experience that we are sharing the recipes with everybody and that it's for sale. The book is $29.99, shipping included.
Customers have to be able to click and buy the book from it.

Coding

Coded - Design and coding required

Number of Pages Required

1 page

Font styles to use
Sans Serif

Requirements
Must have
• Same colors as the cookbook

```html
<!DOCTYPE html>
<html lang="en">
<head>
<meta charset="utf-8">
<title>Brambles Sandwiches – Your Favorite Recipes In One Book</title>
<link rel="stylesheet" href="https://fonts.googleapis.com/css2?family=Oswald:wght@500;600&family=Quicksand:wght@500;600;700&display=swap">
<style>
:root{
  --pink:#c41f5a;
  --pink-dark:#a3164a;
  --brown:#7b3b10;
  --brown-deep:#3f1a05;
  --ink:#3b2314;
  --wood-dark:#1a0f0a;
  --wood-mid:#3a2417;
  --table:#8a5a34;
  --white:#ffffff;
}
*{margin:0;padding:0;box-sizing:border-box}
html,body{width:1200px;height:3221px;overflow:hidden;background:var(--white)}
body{font-family:"Quicksand",sans-serif;color:var(--ink);letter-spacing:.06em}
.page{position:relative;width:1200px;height:3221px;overflow:hidden}
.abs{position:absolute}
.heading{font-family:"Oswald",sans-serif;font-weight:600;text-transform:uppercase;letter-spacing:.08em}
.btn{position:absolute;display:flex;align-items:center;justify-content:center;width:152px;height:36px;border-radius:18px;background:var(--pink);color:var(--white);font-family:"Oswald",sans-serif;font-weight:500;font-size:15px;letter-spacing:.14em;text-decoration:none;text-transform:uppercase}
.quote-badge{position:absolute;width:60px;height:60px;border-radius:50%;background:var(--pink);color:var(--white);font-family:"Oswald",sans-serif;font-size:52px;line-height:78px;text-align:center;box-shadow:0 6px 14px rgba(0,0,0,.18)}

/* hero */
.hero{left:0;top:0;width:1200px;height:618px;background:linear-gradient(180deg,#2b1a11 0%,var(--wood-dark) 35%,#21140d 62%,var(--wood-mid) 78%,var(--table) 86%,#5d3a20 100%)}
.hero-title{left:150px;top:152px;width:480px;font-size:44px;line-height:56px;letter-spacing:.05em;white-space:nowrap;color:var(--white)}
.hero-sub{left:150px;top:288px;width:420px;font-size:13px;line-height:19px;color:var(--white)}
.hero-includes{left:150px;top:348px;font-size:16px;font-weight:600;color:var(--white);letter-spacing:.1em;text-transform:uppercase}
.hero-includes span{color:var(--pink);font-size:21px}
.hero-tags{left:150px;top:384px;display:flex;gap:30px;font-size:13px;color:var(--white)}
.hero-tags div{display:flex;align-items:center;gap:7px}
.price{left:641px;top:146px;width:138px;height:138px;border-radius:50%;background:radial-gradient(circle at 40% 35%,#d8336f,var(--pink) 55%,var(--pink-dark));color:var(--white);text-align:center;box-shadow:0 8px 20px rgba(0,0,0,.35)}
.price .amount{font-family:"Oswald",sans-serif;font-weight:500;font-size:36px;margin-top:40px;line-height:40px}
.price .amount small{font-size:18px}
.price .ship{font-size:10px;line-height:12px;margin-top:4px}
.hero-book{left:709px;top:69px;width:345px;height:487px;border-radius:6px 14px 6px 6px;background:linear-gradient(160deg,#eef2f5 0%,#dfe6ea 45%,#c99a5e 70%,#e8ecef 100%);box-shadow:10px 10px 30px rgba(0,0,0,.45)}
.hero-burger{left:900px;top:412px;width:300px;height:232px;border-radius:46% 40% 30% 50%;background:radial-gradient(ellipse at 55% 40%,#d89a3c,#a35a1e 55%,#3d2412 90%)}
.partners-tab{left:472px;top:598px;width:256px;height:47px;border-radius:0 0 40px 40px;background:var(--brown-deep);color:var(--white);font-size:22px;text-align:center;line-height:44px;letter-spacing:.12em}

/* partners */
.partners{left:200px;top:690px;width:800px;height:50px;display:flex;justify-content:space-between;align-items:center}
.partner{font-family:"Quicksand",sans-serif;font-weight:700;font-size:22px;color:#6f6f6f;letter-spacing:.02em}

/* feature */
.feature-photo{left:145px;top:779px;width:459px;height:681px;border-radius:10px 0 0 10px;background:linear-gradient(170deg,#e9c789 0%,#d9a35a 40%,#8a6a3a 70%,#3b2a1a 100%)}
.feature-panel{left:604px;top:779px;width:451px;height:650px;border-radius:0 10px 10px 0;background:linear-gradient(180deg,var(--brown) 0%,var(--brown-deep) 100%);color:var(--white)}
.feature-panel .heading{font-size:24px;letter-spacing:.1em}
.feature-panel p{font-size:13px;line-height:19px;width:380px;margin-top:10px}
.feature-item{position:absolute;left:33px}
.quote-card{left:279px;top:1371px;width:642px;height:134px;border-radius:10px;background:var(--white);box-shadow:0 10px 30px rgba(0,0,0,.14);text-align:center;padding-top:49px;font-size:17px;line-height:29px;font-weight:600;color:#1f1f1f}

/* story */
.story-item{left:145px}
.story-item .kicker{font-size:13px;color:var(--pink)}
.story-item .heading{font-size:24px;color:var(--ink);margin-top:6px}
.story-item p{font-size:13px;line-height:19px;width:390px;margin-top:10px}
.story-photo{left:612px;top:1575px;width:588px;height:537px;background:radial-gradient(ellipse at 60% 50%,#c98a45 0%,#8a5a34 38%,#e6ded6 72%,rgba(255,255,255,0) 100%)}
.books-band{left:0;top:1900px;width:1200px;height:581px}
.books-photo{left:25px;top:1994px;width:637px;height:575px;border-radius:10px;background:linear-gradient(150deg,#dbe6ee 0%,#b7c9d6 40%,#c88a4a 65%,#e7eef3 100%);box-shadow:10px 14px 30px rgba(0,0,0,.4)}
.band-title{left:618px;top:2195px;width:440px;text-align:center;font-size:46px;line-height:52px;color:var(--white)}
.band-sub{left:638px;top:2310px;width:400px;text-align:center;font-size:14px;line-height:20px;color:var(--white)}

/* closing */
.brand{left:500px;top:2606px;width:200px;text-align:center}
.brand .name{font-family:"Oswald",sans-serif;font-weight:600;font-size:28px;line-height:30px;color:var(--ink)}
.brand .tag{font-family:"Oswald",sans-serif;font-weight:500;font-size:12px;letter-spacing:.06em;color:var(--ink)}
.closing-title{left:250px;top:2666px;width:700px;text-align:center;font-size:24px;line-height:32px;color:var(--ink)}
.story-box{left:145px;top:2806px;width:910px;height:415px;border-radius:12px 12px 0 0;background:linear-gradient(180deg,var(--brown) 0%,var(--brown-deep) 100%)}
.story-text{left:270px;top:2866px;width:660px;text-align:center;font-size:17px;line-height:30px;color:var(--white);font-weight:500}
.sandwich-photo{left:50px;top:2994px;width:1094px;height:227px;border-radius:48% 48% 0 0 / 30% 30% 0 0;background:linear-gradient(180deg,#e7b26a 0%,#c9823c 25%,#4f7a2a 55%,#2f5a1a 100%)}
.copyright{left:0;top:3180px;width:1200px;text-align:center;font-size:13px;color:var(--white);letter-spacing:.02em}
.copyright a{color:var(--white)}
</style>
</head>
<body>
<main class="page">

  <section class="abs hero" aria-label="Hero"></section>
  <h1 class="abs heading hero-title">Your Favorite<br>Recipes In One Book</h1>
  <p class="abs hero-sub">Surprise Family And Friends With Branded Sandwiches From Brambles</p>
  <p class="abs hero-includes">Book Includes <span>28 Recipes</span>:</p>
  <div class="abs hero-tags">
    <div><svg width="20" height="14" viewBox="0 0 20 14" fill="none" stroke="#fff" stroke-width="1.4"><path d="M2 7 Q10 1 18 7Z"/><path d="M2 10h16"/><path d="M3 12.5h14"/></svg>Sandwiches</div>
    <div><svg width="20" height="14" viewBox="0 0 20 14" fill="none" stroke="#fff" stroke-width="1.4"><path d="M2 5h16l-3 6H5z"/><path d="M8 2l4 3"/></svg>Sauces</div>
    <div><svg width="20" height="16" viewBox="0 0 20 16" fill="none" stroke="#fff" stroke-width="1.4"><path d="M3 7 Q10 0 17 7Z"/><path d="M2 10h16"/><path d="M3 13h14"/></svg>Burgers</div>
  </div>
  <a class="btn" href="#order" style="left:150px;top:430px">Byu Now</a>
  <div class="abs hero-book" role="img" aria-label="Cookbook cover with a stacked sandwich"></div>
  <div class="abs hero-burger" role="img" aria-label="Burger on a wooden board"></div>
  <div class="abs price"><div class="amount"><small>$</small>29.99</div><div class="ship">Free<br>Shipping</div></div>
  <div class="abs heading partners-tab">Partners</div>

  <div class="abs partners">
    <span class="partner">Goldarch</span>
    <span class="partner">Fizzwell</span>
    <span class="partner">Bluecap</span>
    <span class="partner">Market Town</span>
  </div>

  <div class="abs feature-photo" role="img" aria-label="Hand lifting a toasted cheese sandwich"></div>
  <section class="abs feature-panel">
    <div class="feature-item" style="top:78px">
      <h2 class="heading">Favorite Recipes In One Book</h2>
      <p>Lorem ipsum dolor sit amet, consectetur adipiscing elit. Magna pulvinar vestibulum bibendum dictum dignissim dictum auctor fusce eget.</p>
    </div>
    <div class="feature-item" style="top:206px">
      <h2 class="heading">Favorite Recipes In One Book</h2>
      <p>Quis blandit sem viverra aliquam posuere risus semper eu. Faucibus mattis ipsum imperdiet molestie.</p>
    </div>
    <div class="feature-item" style="top:336px">
      <h2 class="heading">Favorite Recipes In One Book</h2>
      <p>Dignissim ipsum vivamus sed habitant sed tincidunt nibh sed a. Tellus consequat adipiscing elit nisi. Eget in ullamcorper id pharetra, nisl.</p>
    </div>
  </section>
  <a class="btn" href="#order" style="left:637px;top:1245px">Byu Now</a>
  <blockquote class="abs quote-card">We Truly Hope You Will Enjoy Making These Sandwiches<br>Just As Much As We Did.</blockquote>
  <div class="quote-badge" style="left:569px;top:1341px">”</div>

  <div class="abs story-item" style="top:1648px">
    <p class="kicker">Lorem ipsum dolor</p>
    <h2 class="heading">Favorite Recipes In One Book</h2>
    <p>Lorem ipsum dolor sit amet, consectetur adipiscing elit. Magna pulvinar vestibulum bibendum dictum dignissim dictum auctor fusce eget.</p>
  </div>
  <div class="abs story-item" style="top:1811px">
    <p class="kicker">Lorem ipsum dolor</p>
    <h2 class="heading">Favorite Recipes In One Book</h2>
    <p>Quis blandit sem viverra aliquam posuere risus semper eu. Faucibus mattis ipsum imperdiet molestie.</p>
  </div>

  <svg class="abs books-band" width="1200" height="581" viewBox="0 0 1200 581" aria-hidden="true">
    <defs>
      <linearGradient id="bandFill" x1="0" y1="0" x2="1" y2="0">
        <stop offset="0" stop-color="#4a2a17"/>
        <stop offset=".55" stop-color="#3a2113"/>
        <stop offset="1" stop-color="#5a2608"/>
      </linearGradient>
    </defs>
    <path d="M0 12 C150 150 450 220 800 215 C1000 212 1120 190 1200 160 L1200 581 L0 581 Z" fill="url(#bandFill)"/>
  </svg>
  <div class="abs story-photo" role="img" aria-label="Hand holding a bitten burger"></div>
  <div class="abs books-photo" role="img" aria-label="Two copies of the cookbook standing on a table"></div>
  <h2 class="abs heading band-title">Favorite Recipes<br>In One Book</h2>
  <p class="abs band-sub">Surprise Family And Friends With Branded Sandwiches From Brambles</p>
  <a class="btn" id="order" href="#order" style="left:762px;top:2372px">Byu Now</a>

  <div class="abs brand"><div class="name">BRAMBLES</div><div class="tag">SANDWICHES</div></div>
  <h2 class="abs heading closing-title">Quis Blandit Sem Viverra Aliquam Posuere<br>Risus Semper Eu.</h2>

  <section class="abs story-box"></section>
  <p class="abs story-text">Unfortunately, we can’t open another Brambles, but we can offer you this collection of our recipes for you to try out at home with your family and friends.</p>
  <div class="quote-badge" style="left:569px;top:2776px">”</div>
  <div class="abs sandwich-photo" role="img" aria-label="Close-up of a long sandwich with fresh greens"></div>
  <p class="abs copyright">Copyright 2022. <a href="#">Brambles Sandwiches</a> | All Rights Reserved</p>

</main>
</body>
</html>
```